MEDICAL CLINIC LETTERHEAD

Design is a letterhead for a non-profit medical center. The name of the clinic is VITARIDGE Community Health Center. Although the full name must be included, the community health center part is more of a description and should be less visible - i attached an example of what I mean by that (ATTACHED IMAGE IS AN EXAMPLE OF FONT SIZES NOT A DESIGN IDEA). Please design something modern, cool looking and unique because I can always download free templates.
Phone, email, website and etc will be added later.

Industry/Entity Type

MEDICAL

```html
<!DOCTYPE html>
<html lang="en">
<head>
<meta charset="utf-8">
<title>VITARIDGE Community Health Center Letterhead</title>
<link rel="stylesheet" href="https://fonts.googleapis.com/css2?family=Lato:wght@400;700&family=Figtree:wght@400;500&family=Parisienne&display=swap">
<style>
  :root {
    --backdrop: #e4e4e4;
    --paper: #ffffff;
    --paper-shade: #f3f2f2;
    --navy: #1b2748;
    --gold: #b3935a;
    --ink: #3a3a3a;
    --ink-dark: #111111;
    --icon: #a08c6a;
  }
  * { margin: 0; padding: 0; box-sizing: border-box; }
  html, body {
    width: 1153px; height: 1200px; overflow: hidden;
    background: var(--backdrop);
  }
  .letterhead {
    position: absolute; left: 165px; top: 25px;
    width: 822px; height: 1150px;
    background: radial-gradient(ellipse at 55% 45%, var(--paper) 25%, var(--paper-shade) 100%);
    box-shadow: 0 4px 18px rgba(0,0,0,0.18);
    overflow: hidden;
    font-family: "Lato", sans-serif;
    color: var(--ink);
  }
  .brand {
    position: absolute; left: 60px; top: 62px;
    color: var(--navy); font-family: "Lato", sans-serif; font-weight: 700;
  }
  .brand-name { display: flex; align-items: center; gap: 10px; font-size: 46px; letter-spacing: 1px; line-height: 1; }
  .brand-mark { width: 14px; height: 14px; background: var(--gold); }
  .brand-descriptor { margin-top: 8px; font-size: 10px; letter-spacing: 2.4px; text-transform: uppercase; }
  .contact {
    position: absolute; left: 561px; top: 47px;
    border-left: 1.5px solid var(--gold);
    padding-left: 12px;
    font-family: "Figtree", sans-serif; font-size: 13.5px; color: var(--ink-dark);
    font-style: normal; line-height: 1.35;
  }
  .contact-org { margin-bottom: 6px; }
  .contact-line { display: flex; align-items: center; gap: 8px; height: 19.5px; }
  .contact-line svg { width: 14px; height: 14px; fill: var(--icon); flex: none; }
  .letter {
    position: absolute; left: 63px; width: 696px;
    font-size: 15.6px; line-height: 17.7px;
  }
  .date { top: 255px; }
  .recipient { top: 293px; }
  .recipient p + p { margin-top: 18px; }
  .salutation { top: 427px; font-size: 20px; font-weight: 700; }
  .body { top: 470px; text-align: justify; }
  .body p + p { margin-top: 17px; }
  .closing { top: 789px; }
  .signature {
    position: absolute; left: 66px; top: 828px;
    font-family: "Parisienne", cursive; font-size: 38px; color: var(--ink-dark);
  }
  .footer-band {
    position: absolute; left: 0; bottom: 0; width: 822px; height: 150px;
    background: linear-gradient(to bottom, var(--navy) 0%, var(--navy) 18%, var(--gold) 55%, var(--gold) 100%);
  }
</style>
</head>
<body>
  <main class="letterhead">
    <header>
      <div class="brand">
        <div class="brand-name"><span>VITARIDGE</span><span class="brand-mark"></span></div>
        <div class="brand-descriptor">Community Health Center</div>
      </div>
      <address class="contact">
        <div class="contact-org">VITARIDGE Community<br>Health Center</div>
        <div class="contact-line">
          <svg viewBox="0 0 16 16" aria-hidden="true"><path d="M2 6c0-2 3-3 6-3s6 1 6 3v1h-3V6H5v1H2z M4 8h8l2 5H2z"/></svg>
          <span>555-014-2290</span>
        </div>
        <div class="contact-line">
          <svg viewBox="0 0 16 16" aria-hidden="true"><path d="M1 4h14v9H1z M2 5l6 4 6-4" stroke="#fff" stroke-width="1"/></svg>
          <span>hello@vitaridge-mail.org</span>
        </div>
        <div class="contact-line">
          <svg viewBox="0 0 16 16" aria-hidden="true"><circle cx="8" cy="8" r="6.5"/><path d="M1.5 8h13M8 1.5c-3 3-3 10 0 13M8 1.5c3 3 3 10 0 13" stroke="#fff" stroke-width="0.8" fill="none"/></svg>
          <span>www.vitaridge-care.org</span>
        </div>
      </address>
    </header>

    <p class="letter date">Feb-03-2022</p>
    <div class="letter recipient">
      <p>Mr, Daniel Reeve<br>President</p>
      <p>Harbor Lane Group<br>48 Alder Road, Suite# 6<br>Town, State, 430187</p>
    </div>
    <h1 class="letter salutation">Dear Mr, Daniel</h1>
    <div class="letter body">
      <p>Lorem ipsum dolor sit amet, consectetur adipisicing elit, sed do eiusmod tempor incididunt ut labore et dolore magna aliqua. Ut enim ad minim veniam, quis nostrud exercitation ullamco laboris nisi ut aliquip ex ea commodo consequat. Duis aute irure dolor in reprehenderit in voluptate velit esse cillum dolore eu fugiat nulla pariatur.</p>
      <p>Lorem ipsum dolor sit amet, consectetur adipisicing elit, sed do eiusmod tempor incididunt ut labore et dolore magna aliqua. Ut enim ad minim veniam, quis nostrud exercitation ullamco laboris nisi ut aliquip ex ea commodo consequat. Duis aute irure dolor in reprehenderit in voluptate velit esse cillum dolore eu fugiat nulla pariatur.</p>
      <p>Lorem ipsum dolor sit amet, consectetur adipisicing elit, sed do eiusmod tempor incididunt ut labore et dolore magna aliqua. Ut enim ad minim veniam, quis nostrud exercitation ullamco laboris nisi ut aliquip ex ea commodo consequat.</p>
      <p>Excepteur sint occaecat cupidatat non proident, sunt in culpa qui officia deserunt mollit anim id est laborum. re et dolore magnam aliquam quaerat voluptatem.</p>
    </div>
    <p class="letter closing">Regards</p>
    <p class="signature">Laura Bennett</p>

    <div class="footer-band" role="img" aria-label="Decorative navy and gold footer band"></div>
  </main>
</body>
</html>
```